BOLD & MINIMALIST DESIGN NEEDED

We want a very bold but minimalistic business card design that is impactful and utilizes both sides of the business card. Our current logo is included for your use.

We want bold fonts and good use of negative space. We don't want the logo to overpower the design.

Target Market(s)

Professionals who are building new commercial buildings.

Industry/Entity Type

Construction

Contact Information for Business Card

Name, Title, email, office phone, cell phone, website

Font styles to use
Serif
Sans Serif

Requirements
Must have
• Bold design!

```html
<!DOCTYPE html>
<html lang="en">
<head>
<meta charset="UTF-8">
<title>Ridgeway Design + Build — Business Card</title>
<link rel="stylesheet" href="https://fonts.googleapis.com/css2?family=Montserrat:wght@400;500;800&display=swap">
<style>
  :root {
    --stage: #b9b9b9;
    --card-black: #1e1e1e;
    --card-white: #ffffff;
    --brand-green: #7ac943;
    --brand-green-light: #c9eab0;
    --text-light: #f2f2f2;
    --text-dark: #1a1a1a;
  }
  * { margin: 0; padding: 0; box-sizing: border-box; }
  html, body { width: 1200px; height: 802px; overflow: hidden; }
  body {
    background: var(--stage);
    font-family: "Montserrat", sans-serif;
    display: flex;
    align-items: center;
    justify-content: center;
    gap: 40px;
  }
  .card {
    width: 540px;
    height: 310px;
    border-radius: 22px;
    overflow: hidden;
    position: relative;
    box-shadow: 0 14px 30px rgba(0,0,0,0.25);
  }

  /* Contact side */
  .card--contact { display: flex; background: var(--card-black); }
  .brand-panel {
    width: 44%;
    background: var(--card-white);
    display: flex;
    align-items: center;
    justify-content: center;
  }
  .divider {
    position: absolute;
    left: 44%;
    top: 78px;
    width: 12px;
    height: 150px;
    background: linear-gradient(180deg, var(--brand-green), var(--brand-green-light));
  }
  .contact-panel {
    flex: 1;
    padding: 62px 0 0 44px;
    color: var(--text-light);
  }
  .person-name {
    font-weight: 800;
    font-size: 25px;
    letter-spacing: 0.5px;
    color: var(--brand-green);
    text-transform: uppercase;
    line-height: 1;
  }
  .person-title {
    font-size: 14px;
    font-weight: 400;
    margin-top: 6px;
  }
  .rule {
    width: 10px;
    height: 1px;
    background: var(--text-light);
    margin: 14px 0 10px;
  }
  .contact-list { list-style: none; }
  .contact-list li {
    display: flex;
    align-items: center;
    gap: 9px;
    font-size: 13.5px;
    line-height: 1.85;
  }
  .contact-list svg { width: 12px; height: 12px; flex: none; }
  .accent { color: var(--brand-green); }

  /* Wordmark */
  .wordmark { display: flex; flex-direction: column; align-items: center; gap: 4px; }
  .wordmark__row { display: flex; align-items: center; gap: 8px; }
  .wordmark__square { width: 14px; height: 14px; background: var(--brand-green); }
  .wordmark__name, .wordmark__sub {
    font-weight: 800;
    text-transform: uppercase;
    line-height: 1;
  }
  .wordmark__name { font-size: 30px; }
  .wordmark__sub { font-size: 12px; letter-spacing: 5px; }
  .wordmark--dark .wordmark__name, .wordmark--dark .wordmark__sub { color: var(--text-dark); }

  /* Logo side */
  .card--logo {
    background: var(--card-black);
    display: flex;
    align-items: center;
    justify-content: center;
  }
  .wordmark--light .wordmark__name, .wordmark--light .wordmark__sub { color: var(--text-light); }
  .wordmark--light .wordmark__name { font-size: 44px; }
  .wordmark--light .wordmark__sub { font-size: 16px; letter-spacing: 8px; }
  .wordmark--light .wordmark__square { width: 20px; height: 20px; }
</style>
</head>
<body>

  <section class="card card--contact">
    <div class="brand-panel">
      <div class="wordmark wordmark--dark">
        <div class="wordmark__row">
          <span class="wordmark__square"></span>
          <span class="wordmark__name">Ridgeway</span>
        </div>
        <span class="wordmark__sub">Design + Build</span>
      </div>
    </div>
    <span class="divider"></span>
    <div class="contact-panel">
      <h1 class="person-name">Marcus Hale</h1>
      <p class="person-title">CEO/Founder</p>
      <div class="rule"></div>
      <ul class="contact-list">
        <li>
          <svg viewBox="0 0 12 12"><path fill="var(--brand-green)" d="M2.5 1l2 2-1 1.3a7 7 0 0 0 4.2 4.2L9 7.5l2 2-1.3 1.5C5 11 1 7 1 2.3z"/></svg>
          07 5120 4400
        </li>
        <li>
          <svg viewBox="0 0 12 12"><rect x="3" y="0.8" width="6" height="10.4" rx="1.2" fill="none" stroke="var(--brand-green)" stroke-width="1.3"/></svg>
          0412 667 905
        </li>
        <li>
          <svg viewBox="0 0 12 12"><rect x="0.8" y="2.5" width="10.4" height="7" fill="var(--brand-green)"/><path d="M1 3l5 3.6L11 3" fill="none" stroke="var(--card-black)" stroke-width="1"/></svg>
          info@ridgewaybuild.com
        </li>
        <li>
          <svg viewBox="0 0 12 12"><circle cx="6" cy="6" r="5" fill="none" stroke="var(--brand-green)" stroke-width="1.3"/><path d="M1 6h10M6 1c-2.5 3-2.5 7 0 10M6 1c2.5 3 2.5 7 0 10" fill="none" stroke="var(--brand-green)" stroke-width="1"/></svg>
          <span>www.<span class="accent">ridgewaybuild</span>.com</span>
        </li>
      </ul>
    </div>
  </section>

  <section class="card card--logo">
    <div class="wordmark wordmark--light">
      <div class="wordmark__row">
        <span class="wordmark__square"></span>
        <span class="wordmark__name">Ridgeway</span>
      </div>
      <span class="wordmark__sub">Design + Build</span>
    </div>
  </section>

</body>
</html>
```